Recruiting ad for Caregivers and Nurses

We need a few amazing, fun, catchy, creative recruiting ads for Caregivers and Nurses to care for homecare patients on the island of Oahu, in Hawaii. We are an in home care company called Palmer Homecare. Our care services are provided 24/7, so we need staff that can work days, nights, weekdays, weekends. We need catchy fun ads to entice caregivers and nurses to call our office to inquire about jobs available. Our patients age range is from babies to seniors. We need caregivers and nurses for basic patient care (bathing, dressing, ambulating, preparing meals, medication reminders, light housekeeping) and complex patients (oxygen, tube feeding, injections, vents, wound care). Here are some bullets to consider including:
*Full-time and Part-time Positions Available (days, nights, weekdays, weekends)
*Sign-On Bonus Programs Offered up to $500
*Refer a Friend Bonus Program
*Holiday Pay
*2 Health Plans to Choose from
*Island-Wide Locations
*All PPE Provided (masks, gloves, etc)
*401K Program
*Tuition Benefits

```html
<!DOCTYPE html>
<html lang="en">
<head>
<meta charset="utf-8">
<title>Palmer Homecare – Caregiver Recruiting Ad</title>
<link href="https://fonts.googleapis.com/css2?family=Montserrat:wght@500;600;700;800;900&family=Roboto+Condensed:wght@500;700&display=swap" rel="stylesheet">
<style>
  :root {
    --teal: #12735f;
    --teal-dark: #0f463f;
    --teal-line: #2fa37f;
    --mint: #3cc3a0;
    --salmon: #f29a80;
    --ink: #121212;
    --white: #ffffff;
    --fleece: #dcdcd8;
  }
  * { margin: 0; padding: 0; box-sizing: border-box; }
  html, body { width: 833px; height: 1200px; overflow: hidden; background: #ffffff; }
  .ad {
    position: relative;
    width: 833px; height: 1200px;
    overflow: hidden;
    font-family: "Montserrat", sans-serif;
    color: var(--white);
    background: var(--teal);
  }
  .hero-photo {
    position: absolute; left: 0; top: 0; width: 833px; height: 536px;
    background:
      radial-gradient(ellipse 190px 210px at 185px 230px, #efc6ad 0%, #e6b79e 55%, rgba(230,183,158,0) 100%),
      radial-gradient(ellipse 260px 240px at 150px 430px, #dfe7f0 0%, #d3dde8 60%, rgba(211,221,232,0) 100%),
      linear-gradient(135deg, #e4e4e0 0%, var(--fleece) 50%, #cfcfca 100%);
  }
  .hero-rule-vertical {
    position: absolute; left: 389px; top: 58px; width: 9px; height: 478px;
    background: var(--teal);
  }
  .hero-headline {
    position: absolute; left: 424px; top: 109px;
    font-weight: 800; font-size: 74px; line-height: 99px;
    letter-spacing: -3px; color: var(--ink); white-space: nowrap;
  }
  .hero-rule-under {
    position: absolute; left: 437px; top: 418px; width: 317px; height: 21px;
    background: var(--teal);
  }
  .meet {
    position: absolute; left: 0; top: 570px; width: 833px; text-align: center;
    font-weight: 800; font-size: 44px; letter-spacing: 0.5px;
  }
  .invite {
    position: absolute; left: 0; top: 634px; width: 833px; text-align: center;
    font-weight: 700; font-size: 36px;
  }
  .invite .dot {
    display: inline-block; width: 26px; height: 26px; border: 4px solid var(--mint);
    border-radius: 50%; margin-right: 18px; vertical-align: 2px;
  }
  .divider { position: absolute; left: 111px; width: 616px; height: 2px; background: var(--teal-line); }
  .divider.top { top: 704px; }
  .divider.mid { top: 821px; }
  .divider.foot { top: 1130px; width: 464px; }
  .positions {
    position: absolute; left: 0; top: 716px; width: 833px; text-align: center;
    font-weight: 500; font-size: 23.5px;
  }
  .shifts {
    position: absolute; left: 0; top: 766px; width: 833px;
    display: flex; justify-content: center; gap: 40px;
    font-weight: 500; font-size: 15.5px; letter-spacing: 0.6px;
  }
  .shift { display: flex; align-items: center; gap: 14px; }
  .shift svg { width: 26px; height: 26px; }
  .condensed { font-family: "Roboto Condensed", sans-serif; font-weight: 700; }
  .referral {
    position: absolute; left: 45px; top: 845px; display: flex; align-items: center; gap: 16px;
  }
  .referral-badge { width: 52px; height: 52px; }
  .referral-text { font-size: 16.5px; line-height: 20px; }
  .bonus-ticket { position: absolute; left: 269px; top: 800px; width: 440px; height: 140px; }
  .bonus-text {
    position: absolute; left: 318px; top: 862px; width: 306px; text-align: center;
    font-size: 15.5px; white-space: nowrap;
  }
  .bonus-text .accent { color: var(--mint); }
  .bonus-amount {
    position: absolute; left: 640px; top: 856px; width: 76px; text-align: center;
    font-weight: 700; font-size: 21px;
  }
  .bonus-amount small { font-size: 12px; vertical-align: 3px; }
  .benefits {
    position: absolute; left: 86px; list-style: none;
    font-size: 16.5px;
  }
  .benefits li { display: flex; align-items: center; gap: 12px; height: 29.5px; }
  .benefits svg { width: 19px; height: 19px; flex: none; }
  .benefits.first { top: 946px; }
  .benefits.second { top: 1051px; }
  .retirement-badge { position: absolute; left: 388px; top: 943px; width: 102px; height: 102px; }
  .retirement-label {
    position: absolute; left: 388px; top: 965px; width: 102px; text-align: center;
  }
  .retirement-label .big { font-weight: 800; font-size: 21px; line-height: 24px; display: block; }
  .retirement-label .small { font-family: "Roboto Condensed", sans-serif; font-weight: 500; font-size: 15px; color: var(--salmon); display: block; }
  .nurse-photo {
    position: absolute; left: 516px; top: 922px; width: 317px; height: 278px;
    background:
      radial-gradient(ellipse 90px 150px at 250px 170px, #f4f6f8 0%, #e9edf0 60%, rgba(233,237,240,0) 100%),
      linear-gradient(120deg, #eeeeee 0%, #e4e4e4 60%, #d9dde2 100%);
  }
  .brand-name {
    position: absolute; left: 540px; top: 1030px; width: 160px; text-align: center;
    font-weight: 700; font-size: 22px; line-height: 26px; color: var(--teal);
  }
  .website {
    position: absolute; left: 111px; top: 1150px;
    font-weight: 600; font-size: 17.5px; letter-spacing: 0.3px;
  }
</style>
</head>
<body>
<main class="ad">
  <div class="hero-photo" role="img" aria-label="Photo of a baby in a pale blue dotted onesie lying on a white fleece blanket, staring at the camera"></div>
  <div class="hero-rule-vertical"></div>
  <h1 class="hero-headline">TOM<br>LOVES TO<br>STARE.</h1>
  <div class="hero-rule-under"></div>

  <p class="meet">MEET TOM AND MANY OTHERS</p>
  <p class="invite"><span class="dot"></span>be our caregiver</p>

  <div class="divider top"></div>
  <p class="positions">FULL-TIME and PART-TIME Positions Available</p>
  <div class="shifts">
    <span class="shift">
      <svg viewBox="0 0 26 26"><circle cx="13" cy="13" r="6" fill="none" stroke="#f29a80" stroke-width="3"/><g stroke="#f29a80" stroke-width="3" stroke-linecap="round"><line x1="13" y1="1.5" x2="13" y2="4"/><line x1="13" y1="22" x2="13" y2="24.5"/><line x1="1.5" y1="13" x2="4" y2="13"/><line x1="22" y1="13" x2="24.5" y2="13"/><line x1="4.9" y1="4.9" x2="6.6" y2="6.6"/><line x1="19.4" y1="19.4" x2="21.1" y2="21.1"/><line x1="4.9" y1="21.1" x2="6.6" y2="19.4"/><line x1="19.4" y1="6.6" x2="21.1" y2="4.9"/></g></svg>
      days
    </span>
    <span class="shift">
      <svg viewBox="0 0 26 26"><path d="M16 3a10 10 0 1 0 7 16A8.5 8.5 0 0 1 16 3z" fill="#ffffff"/></svg>
      nights
    </span>
    <span class="shift">
      <svg viewBox="0 0 26 26"><rect x="3" y="5" width="20" height="18" rx="2" fill="#3cc3a0"/><rect x="7" y="2" width="3" height="5" rx="1" fill="#3cc3a0"/><rect x="16" y="2" width="3" height="5" rx="1" fill="#3cc3a0"/><g fill="#12735f"><rect x="6" y="11" width="3" height="3"/><rect x="11.5" y="11" width="3" height="3"/><rect x="17" y="11" width="3" height="3"/><rect x="6" y="16" width="3" height="3"/><rect x="11.5" y="16" width="3" height="3"/><rect x="17" y="16" width="3" height="3"/></g></svg>
      weekdays
    </span>
    <span class="shift">
      <svg viewBox="0 0 26 26"><circle cx="13" cy="13" r="10" fill="none" stroke="#f29a80" stroke-width="5"/><circle cx="13" cy="13" r="10" fill="none" stroke="#12735f" stroke-width="5" stroke-dasharray="4 11.7" stroke-dashoffset="2"/></svg>
      weekends
    </span>
  </div>
  <div class="divider mid"></div>

  <div class="referral">
    <svg class="referral-badge" viewBox="0 0 52 52"><circle cx="26" cy="26" r="24" fill="none" stroke="#f29a80" stroke-width="3"/><rect x="13" y="17" width="26" height="18" rx="3" fill="#ffffff"/><circle cx="20" cy="24" r="3" fill="#12735f"/><path d="M15.5 32c0-4 9-4 9 0z" fill="#12735f"/><g stroke="#12735f" stroke-width="2"><line x1="27" y1="22" x2="35" y2="22"/><line x1="27" y1="26" x2="35" y2="26"/><line x1="27" y1="30" x2="33" y2="30"/></g></svg>
    <p class="referral-text condensed">Refer a Friend<br>BONUS Program</p>
  </div>

  <svg class="bonus-ticket" viewBox="0 0 440 140">
    <path d="M102 62a27 27 0 0 1 54 0" fill="none" stroke="#3cc3a0" stroke-width="3"/>
    <path d="M0 50H380V96H0V86a17 17 0 0 0 0-26z" fill="#0f463f"/>
    <line x1="24" y1="58" x2="24" y2="90" stroke="#3cc3a0" stroke-width="2" stroke-dasharray="2 4"/>
    <line x1="361" y1="58" x2="361" y2="90" stroke="#3cc3a0" stroke-width="2" stroke-dasharray="2 4"/>
    <circle cx="409" cy="72" r="38" fill="#0f463f"/>
  </svg>
  <p class="bonus-text condensed">SIGN-ON <span class="accent">BONUS</span> Programs offered up to</p>
  <p class="bonus-amount"><small>$</small>500</p>

  <ul class="benefits first condensed">
    <li><svg viewBox="0 0 19 19"><circle cx="9.5" cy="9.5" r="8" fill="none" stroke="#3cc3a0" stroke-width="2"/><path d="M5.5 9.8l2.7 2.7 5-5.2" fill="none" stroke="#3cc3a0" stroke-width="2"/></svg>Holiday Pay</li>
    <li><svg viewBox="0 0 19 19"><circle cx="9.5" cy="9.5" r="8" fill="none" stroke="#3cc3a0" stroke-width="2"/><path d="M5.5 9.8l2.7 2.7 5-5.2" fill="none" stroke="#3cc3a0" stroke-width="2"/></svg>2 Health Plans to Choose from</li>
    <li><svg viewBox="0 0 19 19"><circle cx="9.5" cy="9.5" r="8" fill="none" stroke="#3cc3a0" stroke-width="2"/><path d="M5.5 9.8l2.7 2.7 5-5.2" fill="none" stroke="#3cc3a0" stroke-width="2"/></svg>Island-Wide Locations</li>
  </ul>
  <ul class="benefits second condensed">
    <li><svg viewBox="0 0 19 19"><circle cx="9.5" cy="9.5" r="8" fill="none" stroke="#3cc3a0" stroke-width="2"/><path d="M5.5 9.8l2.7 2.7 5-5.2" fill="none" stroke="#3cc3a0" stroke-width="2"/></svg>All PPE Provided (masks, gloves, etc)</li>
    <li><svg viewBox="0 0 19 19"><circle cx="9.5" cy="9.5" r="8" fill="none" stroke="#3cc3a0" stroke-width="2"/><path d="M5.5 9.8l2.7 2.7 5-5.2" fill="none" stroke="#3cc3a0" stroke-width="2"/></svg>Tuition Benefits</li>
  </ul>

  <svg class="retirement-badge" viewBox="0 0 102 102">
    <defs><clipPath id="badge-inner"><circle cx="51" cy="51" r="47"/></clipPath></defs>
    <path d="M0 78q25-12 50 0t52 0V102H0z" fill="#f29a80" clip-path="url(#badge-inner)"/>
    <circle cx="51" cy="51" r="48.5" fill="none" stroke="#f29a80" stroke-width="3.5"/>
  </svg>
  <p class="retirement-label"><span class="big">401K</span><span class="small">Program</span></p>

  <div class="nurse-photo" role="img" aria-label="Photo of a smiling nurse in a white coat with a stethoscope, reading a clipboard"></div>
  <p class="brand-name">Palmer Homecare</p>

  <div class="divider foot"></div>
  <p class="website">palmercare.com</p>
</main>
</body>
</html>
```